Global Beard Oil Review Business needs a refresh

topwhiskertonic.net is a global business who's mission is to curate all available beard oils from around the world, review and grade them and present this curated collection to the user of the website.

The scope of this job includes the web site design and the design of a suitable logo to be used in the site header.

The existing site can be seen on http://topwhiskertonic.net, however this is a mock-up only the style and logo should NOT be used. This is to give you an idea of the concept of the site only.

This job is for PSD design only.

See attached design brief for detailed design requirements.
Updates

Project Deadline Extended
Reason: Extending deadline by 5 days to allow for final submissions

Target Market(s)

Men's grooming / retail

Industry/Entity Type

Retail

Number of Pages Required

2 page

Font styles to use
Sans Serif

Requirements
Must have
• 1) Comparison Table
• 2) Side Bar
• 3) Header area
• 4) Photo of Delvin Marsk (attached - can be circular or "cut-out")
• 5) Cool beard-oriented custom design background (e.g., stylistic black/brown on brown/orange beard background. I envision this beard background "drawing" rather than photo based)
• (see attached design requirements for details)
Nice to have
• Signature style writing at top with name "Delvin Marsk"
Should not have
• Do NOT use the look & feel or logo from the existing site.

```html
<!DOCTYPE html>
<html lang="en">
<head>
<meta charset="utf-8">
<title>topwhiskertonic.net</title>
<link rel="stylesheet" href="https://fonts.googleapis.com/css2?family=Lobster&family=Ubuntu:wght@400;500&family=Lato:wght@400;700&display=swap">
<style>
:root{
  --teal:#3fb6b4;
  --orange:#f7a03a;
  --brown:#7b5a4e;
  --green:#36a82a;
  --ink:#4a4a4a;
  --muted:#7d7d7d;
  --line:#d9dfe2;
  --pale:#eef2f4;
  --row:#dde6ea;
  --navbar:#e6ecee;
  --footer:#2f3240;
}
*{box-sizing:border-box;margin:0;padding:0}
html,body{width:1200px;height:2296px;overflow:hidden}
body{font-family:'Ubuntu',sans-serif;color:var(--ink);background:#fff;position:relative}
.wrap{width:936px;margin:0 auto;position:relative}

/* header */
.topbar{border-top:3px solid var(--orange);height:81px}
.topbar .wrap{height:78px;display:flex;align-items:center;justify-content:space-between}
.brand{font-family:'Ubuntu',sans-serif;font-size:30px;font-weight:500;color:var(--teal);letter-spacing:-.5px}
.social{display:flex;gap:6px}
.social span{width:27px;height:27px;background:#b9bcbf;border-radius:2px;display:block}
.nav{background:var(--navbar);height:46px}
.nav .wrap{display:flex;align-items:center;height:46px}
.nav a{font-size:14px;color:#555;text-decoration:none;padding:0 18px;height:46px;line-height:46px}
.nav a.active{background:var(--teal);color:#fff;padding:0 22px}
.search{margin-left:auto;width:185px;height:27px;background:#fff;border:1px solid #dde2e4;font-size:12px;color:#aaa;font-style:italic;line-height:25px;padding-left:10px;position:relative}
.search svg{position:absolute;right:7px;top:6px}

/* hero */
.hero{height:390px;position:relative;overflow:hidden}
.hero-photo{position:absolute;inset:0;background:linear-gradient(90deg,#e4e0dc 0%,#ddd7d1 45%,#c9bfb6 70%,#b9ac9f 100%)}
.hero-photo::after{content:"";position:absolute;left:0;right:0;bottom:0;height:80px;background:linear-gradient(180deg,#d8d0c6,#c7b9a9)}
.bottle{position:absolute;background:linear-gradient(180deg,#6d3e22,#3c2010);border-radius:14px 14px 6px 6px}
.hero .wrap{padding-top:92px}
.hero h1{font-family:'Lobster',cursive;font-weight:400;color:var(--brown);font-size:43px;line-height:54px}
.btn{display:inline-block;background:var(--orange);color:#fff;font-size:13px;font-weight:500;text-decoration:none;border-radius:2px}
.hero .btn{margin-top:24px;padding:0 22px;height:38px;line-height:38px}

/* welcome */
.welcome{height:403px}
.welcome .wrap{display:flex;justify-content:space-between;padding-top:40px}
.welcome-text{width:668px}
.welcome h2{font-family:'Lato',sans-serif;font-weight:400;font-size:29px;color:#4b4b4b;padding-bottom:12px;border-bottom:1px solid var(--line)}
.welcome h2 span{color:var(--teal)}
.welcome p{font-size:12.3px;line-height:22px;color:var(--muted);margin-top:18px}
.welcome p+p{margin-top:12px}
.welcome .btn{margin-top:20px;padding:0 19px;height:33px;line-height:33px;font-size:12px}
.portrait{width:268px;height:325px;border:4px solid #dfe4e6;background:linear-gradient(160deg,#d6d6d6,#8a8a8a 55%,#5a5a5a)}

/* table section */
.oils{background:var(--pale);height:742px;padding-top:42px;text-align:center}
.sec-title{font-family:'Lato',sans-serif;font-weight:400;font-size:29px;color:#404040}
.sec-title b{font-weight:700}
.sec-lead{font-size:12.3px;line-height:22px;color:var(--muted);margin:14px auto 0;width:920px}
.grid{margin-top:20px;width:936px;border-collapse:collapse;font-size:12.3px;color:#5a5a5a;text-align:center}
.grid th{height:50px;color:#fff;font-weight:500;font-size:13px}
.grid th.s{background:var(--teal)}
.grid th.r{background:var(--orange)}
.grid th,.grid td{border-right:1px solid rgba(255,255,255,.55)}
.grid td{height:66px;border-right:1px solid #e4eaec}
.grid tr:nth-child(odd) td{background:var(--row)}
.grid tr:nth-child(even) td{background:#fafbfc}
.grid td.t{text-align:left;padding-left:15px;line-height:18px}
.thumb{width:46px;height:46px;margin:0 auto;background:linear-gradient(180deg,#f2ece4 55%,#e9a25c 55%)}
.go{display:inline-block;background:var(--green);color:#fff;font-size:12px;width:82px;height:34px;line-height:34px;border-radius:2px}
.more{display:inline-flex;align-items:center;gap:10px;margin-top:50px;background:#d3d9dc;color:#555;font-size:12.3px;height:35px;padding:0 22px}

/* blog */
.blog{height:498px;padding-top:32px;text-align:center}
.cards{display:flex;justify-content:space-between;margin-top:20px;text-align:left}
.card{width:284px;height:337px;background:var(--pale);position:relative;overflow:hidden}
.card-photo{height:155px}
.card-body{padding:14px 16px}
.card h3{font-family:'Ubuntu',sans-serif;font-weight:400;font-size:18px;line-height:24px;color:var(--teal)}
.meta{font-size:12px;color:#999;margin:8px 0 10px}
.meta i{font-style:normal;margin:0 12px}
.card p{font-size:12px;line-height:22px;color:#555}
.card p b{font-weight:500;color:#333}
.corner{position:absolute;right:0;bottom:0}

/* footer */
.footer{background:var(--footer);height:133px;text-align:center;color:#fff;padding-top:38px}
.footer nav{font-size:13px}
.footer nav a{color:#fff;text-decoration:none}
.footer nav i{font-style:normal;margin:0 20px}
.footer small{display:block;font-size:13px;margin-top:30px}
</style>
</head>
<body>

<header class="topbar">
  <div class="wrap">
    <div class="brand">TopWhiskerTonic.net</div>
    <div class="social"><span></span><span></span><span></span><span></span></div>
  </div>
</header>

<div class="nav">
  <div class="wrap">
    <a class="active" href="#">Home</a>
    <a href="#">About Me</a>
    <a href="#">Our Charter</a>
    <a href="#">Beard Oil Methodology</a>
    <a href="#">BLog</a>
    <div class="search">Search
      <svg width="13" height="13" viewBox="0 0 13 13"><circle cx="5.5" cy="5.5" r="4" fill="none" stroke="#bbb" stroke-width="1.6"/><line x1="8.5" y1="8.5" x2="12" y2="12" stroke="#bbb" stroke-width="1.8"/></svg>
    </div>
  </div>
</div>

<section class="hero">
  <div class="hero-photo" role="img" aria-label="Beard oil dropper bottles standing on a wooden table">
    <div class="bottle" style="left:640px;top:220px;width:90px;height:200px;opacity:.35"></div>
    <div class="bottle" style="left:750px;top:230px;width:90px;height:200px;opacity:.35"></div>
    <div class="bottle" style="left:870px;top:230px;width:120px;height:225px"></div>
  </div>
  <div class="wrap">
    <h1>Simply dummy text<br>The printing and typesetting</h1>
    <a class="btn" href="#">Get Yours Now</a>
  </div>
</section>

<section class="welcome">
  <div class="wrap">
    <div class="welcome-text">
      <h2>Welcome to <span>TopWhiskerTonic</span></h2>
      <p>Sed ut perspiciatis unde omnis iste natus error sit voluptatem accusantium doloremque laudantium, totam rem aperiam, eaque ipsa quae ab illo inventore veritatis et quasi architecto beatae vitae dicta sunt explicabo. Nemo enim ipsam voluptatem quia voluptas sit aspernatur aut odit aut fugit, sed quia consequuntur magni dolores eos qui ratione voluptatem sequi nesciunt. Neque porro quisquam est, qui dolorem ipsum quia dolor sit amet, consectetur, adipisci velit, sed quia non numquam eius modi tempora incidunt ut labore et dolore magnam aliquam quaerat voluptatem.</p>
      <p>Sed ut perspiciatis unde omnis iste natus error sit voluptatem accusantium doloremque laudantium, totam rem aperiam, eaque ipsa quae ab illo inventore veritatis et quasi architecto beatae vitae dicta sunt explicabo.</p>
      <a class="btn" href="#">Read More »</a>
    </div>
    <div class="portrait" role="img" aria-label="Black and white photo of Delvin Marsk giving a thumbs up"></div>
  </div>
</section>

<section class="oils">
  <div class="wrap">
    <h2 class="sec-title">The World’s <b>#1 Beard Oil Authority</b></h2>
    <p class="sec-lead">Here is the master list of beard oils reviewed to date. You can link directly to the corresponding review by clicking on the name of the beard oil. In accordance with our charter, we are actively working to locate and review every single beard oil available on the planet Earth.</p>
    <table class="grid">
      <colgroup><col style="width:135px"><col style="width:100px"><col style="width:66px"><col style="width:78px"><col style="width:78px"><col style="width:78px"><col style="width:75px"><col style="width:75px"><col style="width:75px"><col style="width:75px"><col style="width:101px"></colgroup>
      <thead><tr>
        <th class="s">Supplier</th><th class="s">Name</th><th class="s">Photo</th><th class="s">Origin</th><th class="s">Base Oil</th><th class="s">Scent</th>
        <th class="r">Aroma</th><th class="r">Affect</th><th class="r">Value</th><th class="r">Overall</th><th class="r">Links</th>
      </tr></thead>
      <tbody>
        <tr><td class="t">Allied Whisker Co.</td><td class="t">Timberline</td><td><div class="thumb" role="img" aria-label="Beard oil bottle"></div></td><td>Australia</td><td>Dummy</td><td>Simply</td><td>5</td><td>7</td><td>5</td><td>7</td><td><span class="go">Get Now</span></td></tr>
        <tr><td class="t">Fullform Soaps</td><td class="t">Stonecut Beard Oil</td><td><div class="thumb" role="img" aria-label="Beard oil bottle"></div></td><td>USA</td><td>Simply</td><td>Dummy</td><td>7</td><td>5</td><td>7</td><td>5</td><td><span class="go">Get Now</span></td></tr>
        <tr><td class="t">Stonecut Men’s Grooming</td><td class="t">Axehand</td><td><div class="thumb" role="img" aria-label="Beard oil bottle"></div></td><td>USA</td><td>Simply</td><td>Dummy</td><td>5</td><td>7</td><td>5</td><td>7</td><td><span class="go">Get Now</span></td></tr>
        <tr><td class="t">Bristle Baron</td><td class="t">Stonecut Beard Oil</td><td><div class="thumb" role="img" aria-label="Beard oil bottle"></div></td><td>Australia</td><td>Dummy</td><td>Simply</td><td>7</td><td>5</td><td>7</td><td>5</td><td><span class="go">Get Now</span></td></tr>
        <tr><td class="t">Allied Whisker Co.</td><td class="t">Timberline</td><td><div class="thumb" role="img" aria-label="Beard oil bottle"></div></td><td>Australia</td><td>Dummy</td><td>Simply</td><td>5</td><td>7</td><td>5</td><td>7</td><td><span class="go">Get Now</span></td></tr>
        <tr><td class="t">Fullform Soaps</td><td class="t">Stonecut Beard Oil</td><td><div class="thumb" role="img" aria-label="Beard oil bottle"></div></td><td>USA</td><td>Simply</td><td>Dummy</td><td>7</td><td>5</td><td>7</td><td>5</td><td><span class="go">Get Now</span></td></tr>
      </tbody>
    </table>
    <span class="more">
      <svg width="16" height="16" viewBox="0 0 16 16"><path d="M13 8a5 5 0 1 1-1.5-3.5" fill="none" stroke="#666" stroke-width="1.6"/><path d="M12 1.5v3.5H8.5" fill="none" stroke="#666" stroke-width="1.6"/></svg>
      View More Beard Oil
    </span>
  </div>
</section>

<section class="blog">
  <div class="wrap">
    <h2 class="sec-title">Latest <b>Blog</b></h2>
    <p class="sec-lead">It is a long established fact that a reader will be distracted by the readable content of a page when looking at its layout.</p>
    <div class="cards">
      <article class="card">
        <div class="card-photo" role="img" aria-label="Cloth sample pouch on a wooden table" style="background:linear-gradient(135deg,#c98a4a,#8a5a2e)"></div>
        <div class="card-body">
          <h3>Misty Ridge Beard Oil by Old Pine Grooming</h3>
          <div class="meta">February 12, 2016<i>|</i>Delvin Marsk</div>
          <p><b>Oil Name</b>: Misty Ridge Beard Oil<br><b>Supplier</b>: Old Pine Grooming<br><b>Sample Size</b>: 25ml</p>
        </div>
        <svg class="corner" width="34" height="34" viewBox="0 0 34 34"><polygon points="34,0 34,34 0,34" fill="var(--orange)"/><path d="M22 26h8M26 22v8" stroke="#fff" stroke-width="1.8"/></svg>
      </article>
      <article class="card">
        <div class="card-photo" role="img" aria-label="Dropper of beard oil held outdoors among green trees" style="background:linear-gradient(135deg,#8fa36a,#3f5a2a)"></div>
        <div class="card-body">
          <h3>Outbacker’s Face/Beard Oil by Fullform Soaps</h3>
          <div class="meta">February 12, 2016<i>|</i>Delvin Marsk</div>
          <p><b>Oil Name</b>: Misty Ridge Beard Oil<br><b>Supplier</b>: Old Pine Grooming<br><b>Sample Size</b>: 25ml</p>
        </div>
        <svg class="corner" width="34" height="34" viewBox="0 0 34 34"><polygon points="34,0 34,34 0,34" fill="var(--orange)"/><path d="M22 26h8M26 22v8" stroke="#fff" stroke-width="1.8"/></svg>
      </article>
      <article class="card">
        <div class="card-photo" role="img" aria-label="Beard oil bottle with a note card on a wooden table" style="background:linear-gradient(135deg,#e0c9a6,#a98b63)"></div>
        <div class="card-body">
          <h3>Axehand Oil by Allied Whisker Co.</h3>
          <div class="meta">February 12, 2016<i>|</i>Delvin Marsk</div>
          <p><b>Oil Name</b>: Misty Ridge Beard Oil<br><b>Supplier</b>: Old Pine Grooming<br><b>Sample Size</b>: 25ml</p>
        </div>
        <svg class="corner" width="34" height="34" viewBox="0 0 34 34"><polygon points="34,0 34,34 0,34" fill="var(--orange)"/><path d="M22 26h8M26 22v8" stroke="#fff" stroke-width="1.8"/></svg>
      </article>
    </div>
  </div>
</section>

<footer class="footer">
  <nav><a href="#">Home</a><i>I</i><a href="#">About Me</a><i>I</i><a href="#">Our Charter</a><i>I</i><a href="#">Beard Oil Methodology</a><i>I</i><a href="#">BLog</a></nav>
  <small>Copyright © 2016 Top Whisker Tonic. All rights reserved.</small>
</footer>

</body>
</html>
```